New Business Card Design for Manufacturing

We are an engineering/manufacturing company that offers Advanced machining/assembly/engineering services, as well as innovative products for the heavy duty engine cooling markets.

We are looking to get a new business card designed that is clean and modern looking, but still fits the wide range of technical/skilled work we do.

- We hope to use this design as the base for other design work in new Presentations, web, and print work.

Industry/Entity Type

Engineering

Contact Information for Business Card

Our preferred color of blue is (RGB) 22/71/159 but can vary slightly from that color. Our content will be our Logo and full company name (Vantrell Forge Works, Inc.), company address, name, job title, phone number with extension, cell number, fax number, website, and email address on the cards.
We'd like the full company name next to the logo, but we are open to other interpretations of that layout.
Preferably, we would like the back side to be clean with just our logo, and the front to contain all of the contact information.

Colors
2f74b4
0355a3
85abd2

Requirements
Must have
• - Logo, company name, needed content - We are open to interpretation beyond that.
• - Standard size business card.
• - Horizontal orientation.
• - Enough space for lengthy names / job titles (for example, a job title could read "Directory of Human Resources" or "V.P. of Governmental Affairs"). We need this to look clean, whether the title be short (CEO) or long (as described above).

```html
<!DOCTYPE html>
<html lang="en">
<head>
<meta charset="utf-8">
<title>Vantrell Forge Works – Business Card</title>
<link href="https://fonts.googleapis.com/css2?family=Lato:wght@400;700;900&family=Archivo+Black&display=swap" rel="stylesheet">
<style>
  :root {
    --brand-blue: #0355a3;
    --brand-mid: #2f74b4;
    --brand-light: #85abd2;
    --ink: #1a1a1a;
    --paper: #ffffff;
    --stage: #3a3a3a;
  }
  * { box-sizing: border-box; margin: 0; padding: 0; }
  html, body { width: 1200px; height: 1200px; overflow: hidden; }
  body {
    background: var(--stage);
    font-family: "Lato", sans-serif;
    position: relative;
  }
  .card {
    position: absolute;
    width: 770px;
    height: 440px;
    overflow: hidden;
    box-shadow: 0 10px 30px rgba(0,0,0,0.45);
  }
  /* Back side */
  .card-back {
    left: 60px;
    top: 100px;
    background: var(--brand-blue);
    color: var(--paper);
  }
  .back-mark {
    position: absolute;
    left: 0; right: 0;
    top: 150px;
    display: flex;
    align-items: center;
    justify-content: center;
    gap: 22px;
  }
  .back-mark .mark-square {
    width: 58px; height: 58px;
    background: var(--paper);
  }
  .back-mark .mark-name {
    font-weight: 900;
    font-size: 92px;
    letter-spacing: 2px;
    line-height: 1;
    color: var(--paper);
  }
  .back-url {
    position: absolute;
    left: 0; right: 0;
    bottom: 60px;
    text-align: center;
    font-size: 22px;
    letter-spacing: 2px;
  }
  /* Front side */
  .card-front {
    left: 370px;
    top: 590px;
    background: var(--paper);
    color: var(--ink);
  }
  .front-header {
    position: absolute;
    top: 48px;
    right: 60px;
    display: flex;
    align-items: center;
    gap: 26px;
  }
  .front-mark {
    display: flex;
    align-items: center;
    gap: 12px;
  }
  .front-mark .mark-square {
    width: 32px; height: 32px;
    background: var(--brand-blue);
  }
  .front-mark .mark-name {
    font-weight: 900;
    font-size: 50px;
    line-height: 1;
    color: var(--brand-blue);
    letter-spacing: 1px;
  }
  .company-name {
    font-family: "Archivo Black", sans-serif;
    font-size: 20px;
    line-height: 1.05;
    text-transform: uppercase;
    color: var(--ink);
  }
  .company-name .suffix { font-size: 10px; vertical-align: baseline; }
  .person {
    position: absolute;
    left: 48px;
    top: 186px;
  }
  .person-name {
    font-weight: 900;
    font-size: 32px;
    color: var(--brand-blue);
    line-height: 1.05;
  }
  .person-title {
    font-size: 20px;
    line-height: 1.2;
    margin-top: 4px;
  }
  .contact-list {
    list-style: none;
    margin-top: 10px;
  }
  .contact-list li {
    display: flex;
    align-items: center;
    gap: 16px;
    font-size: 21px;
    line-height: 1.3;
  }
  .contact-list svg { width: 18px; height: 18px; fill: var(--brand-blue); flex: none; }
  .address {
    position: absolute;
    right: 48px;
    top: 276px;
    text-align: right;
    font-size: 21px;
    line-height: 1.3;
  }
  .front-band {
    position: absolute;
    left: 0; bottom: 0;
    width: 770px; height: 80px;
  }
  .band-url {
    position: absolute;
    left: 48px;
    bottom: 8px;
    font-size: 21px;
    line-height: 1.2;
    letter-spacing: 1.5px;
    color: var(--paper);
  }
</style>
</head>
<body>

  <section class="card card-back" aria-label="Business card, back side">
    <div class="back-mark">
      <span class="mark-square"></span>
      <span class="mark-name">VANTRELL</span>
    </div>
    <p class="back-url">www.vantrellforge.com</p>
  </section>

  <section class="card card-front" aria-label="Business card, front side">
    <header class="front-header">
      <div class="front-mark">
        <span class="mark-square"></span>
        <span class="mark-name">VANTRELL</span>
      </div>
      <p class="company-name">Vantrell<br>Forge<br>Works <span class="suffix">Inc</span></p>
    </header>

    <div class="person">
      <h1 class="person-name">Daniel Okafor</h1>
      <p class="person-title">Directory of Human Resources</p>
      <ul class="contact-list">
        <li>
          <svg viewBox="0 0 24 24" aria-hidden="true"><path d="M6.6 10.8a15 15 0 0 0 6.6 6.6l2.2-2.2c.3-.3.7-.4 1-.2 1.1.4 2.3.6 3.6.6.6 0 1 .4 1 1V20c0 .6-.4 1-1 1C10.6 21 3 13.4 3 4c0-.6.4-1 1-1h3.5c.6 0 1 .4 1 1 0 1.3.2 2.5.6 3.6.1.3 0 .7-.2 1z"/></svg>
          <span>555 014 2200</span>
        </li>
        <li>
          <svg viewBox="0 0 24 24" aria-hidden="true"><path d="M7 2h10a1 1 0 0 1 1 1v18a1 1 0 0 1-1 1H7a1 1 0 0 1-1-1V3a1 1 0 0 1 1-1zm1 2v14h8V4zm4 15.2a1 1 0 1 0 0 2 1 1 0 0 0 0-2z"/></svg>
          <span>555 014 2201</span>
        </li>
        <li>
          <svg viewBox="0 0 24 24" aria-hidden="true"><path d="M7 3h10v5H7zM4 9h16a2 2 0 0 1 2 2v6h-4v4H6v-4H2v-6a2 2 0 0 1 2-2zm4 7v3h8v-3z"/></svg>
          <span>555 014 2203</span>
        </li>
        <li>
          <svg viewBox="0 0 24 24" aria-hidden="true"><path d="M2 5h20v14H2zm2 2v.5l8 5.5 8-5.5V7zm0 3v7h16v-7l-8 5.5z"/></svg>
          <span>info@vantrellforge.com</span>
        </li>
      </ul>
    </div>

    <p class="address">418 Calder Road<br>Houston, TX 77041</p>

    <svg class="front-band" viewBox="0 0 770 80" aria-hidden="true">
      <polygon points="0,38 655,38 643,80 0,80" fill="var(--brand-blue)"/>
      <polygon points="668,18 700,18 690,58 658,58" fill="var(--brand-light)"/>
      <polygon points="712,0 770,0 770,45 700,45" fill="var(--brand-blue)"/>
    </svg>
    <p class="band-url">www.vantrellforge.com</p>
  </section>

</body>
</html>
```